Business Card Design

New business card design

Target Market(s)

Residential & Commercial Property Managers

Industry/Entity Type

Plumbing Services

Contact Information for Business Card

Name - Rowan Keddle, title - Director, Phone Number - 0431 286 517, email - rowan@tbk-plumbing.com.au, Company ABN - 73 215 904 386,

Font styles to use
Sans Serif

Colors
0054AA
0677BA
7BADD7
CADEEF
E8F1F8

```html
<!DOCTYPE html>
<html lang="en">
<head>
<meta charset="utf-8">
<title>TBK Plumbing Services – Business Card</title>
<link href="https://fonts.googleapis.com/css2?family=Roboto:wght@300;400;700&display=swap" rel="stylesheet">
<style>
  :root {
    --bg: #2a2a2a;
    --navy: #0054AA;
    --blue: #0677BA;
    --sky: #7BADD7;
    --mist: #CADEEF;
    --card-white: #E8F1F8;
    --ink: #0b2f57;
    --on-blue: #ffffff;
    --on-blue-soft: #CADEEF;
  }
  * { margin: 0; padding: 0; box-sizing: border-box; }
  html, body { width: 1200px; height: 852px; overflow: hidden; background: var(--bg); }
  body { position: relative; font-family: "Roboto", Arial, sans-serif; }

  .card {
    position: absolute;
    width: 520px;
    height: 300px;
    border-radius: 22px;
    overflow: hidden;
  }

  /* Back of card */
  .card-back { left: 50px; top: 276px; background: var(--navy); }
  .card-back .brand { position: absolute; left: 0; right: 0; top: 96px; text-align: center; color: var(--on-blue); }
  .card-back .brand-tagline { color: var(--mist); }

  /* Shared wordmark */
  .brand-name { font-weight: 300; font-size: 68px; letter-spacing: 4px; line-height: 1; }
  .brand-tagline { font-weight: 300; font-size: 13px; letter-spacing: 7px; margin-top: 6px; }

  /* Front of card */
  .card-front { left: 630px; top: 276px; background: var(--card-white); }
  .card-front .band { position: absolute; inset: 0; }
  .card-front .brand { position: absolute; left: 26px; top: 24px; color: var(--ink); }
  .card-front .brand-name { font-size: 56px; }
  .card-front .brand-tagline { font-size: 11px; letter-spacing: 6px; color: var(--blue); }

  .contact { position: absolute; left: 26px; top: 128px; color: var(--on-blue); }
  .contact-name { font-weight: 700; font-size: 20px; line-height: 24px; }
  .contact-title { font-weight: 300; font-size: 13px; line-height: 16px; color: var(--on-blue-soft); margin: 2px 0 4px; }
  .contact-list { list-style: none; }
  .contact-list li { display: flex; align-items: center; gap: 8px; font-weight: 300; font-size: 12.5px; line-height: 18px; color: var(--on-blue-soft); }
  .contact-list svg { width: 12px; height: 12px; fill: none; stroke: var(--on-blue); stroke-width: 1.4; }
  .contact-list .abn-label { font-weight: 400; font-size: 9px; letter-spacing: 0.5px; color: var(--on-blue); width: 12px; }

  .address { position: absolute; left: 26px; bottom: 14px; font-size: 12.5px; color: var(--ink); }
</style>
</head>
<body>

  <section class="card card-back" aria-label="Card back">
    <div class="brand">
      <div class="brand-name">tbk</div>
      <div class="brand-tagline">plumbing services</div>
    </div>
  </section>

  <section class="card card-front" aria-label="Card front">
    <svg class="band" viewBox="0 0 520 300" aria-hidden="true">
      <path fill="var(--blue)" d="M0 118 H300 L330 40 H520 V190 L300 262 H0 Z"/>
      <path fill="var(--navy)" d="M330 40 H520 V70 H320 Z"/>
    </svg>

    <div class="brand">
      <div class="brand-name">tbk</div>
      <div class="brand-tagline">plumbing services</div>
    </div>

    <div class="contact">
      <div class="contact-name">Rowan Keddle</div>
      <div class="contact-title">Director</div>
      <ul class="contact-list">
        <li>
          <svg viewBox="0 0 12 12"><path d="M2 1.5h2.2l1 2.5-1.3 1a6 6 0 0 0 3.1 3.1l1-1.3 2.5 1V10a1 1 0 0 1-1 1A8.5 8.5 0 0 1 1 2.5a1 1 0 0 1 1-1z"/></svg>
          0431 286 517
        </li>
        <li>
          <svg viewBox="0 0 12 12"><rect x="1" y="2.5" width="10" height="7"/><path d="M1 2.5l5 4 5-4"/></svg>
          rowan@tbk-plumbing.com.au
        </li>
        <li>
          <svg viewBox="0 0 12 12"><circle cx="6" cy="6" r="5"/><ellipse cx="6" cy="6" rx="2.2" ry="5"/><path d="M1 6h10"/></svg>
          www.tbk-plumbing.com.au
        </li>
        <li>
          <svg viewBox="0 0 12 12"><rect x="1.5" y="1" width="9" height="10"/><path d="M3.5 4h5M3.5 6h5M3.5 8h3"/></svg>
          ABN 73 215 904 386
        </li>
      </ul>
    </div>

    <div class="address">12 Harbour Rd, Brookvale NSW 2100</div>
  </section>

</body>
</html>
```